Human Resource Consulting practice needs a business card design

We need a business card design (double sided colour) for our Human Resource (HR) consulting practice in regional New South Wales, australia. Our business name is Staff Compass. We support small and medium business across the Mid North Coast of New South Wales by providing them with outsourced HR support, services and products to help them achieve compliance with workplace legislation and across all areas of the employment lifecycle from recruitment to termination and everything in between. Our corporate colours are hot pink and black. The final design should communicate professionalism, trust, people focus.
I have attached the current (old) business card for your reference.

Target Market(s)

Business owners and high level managers

Industry/Entity Type

Business

Contact Information for Business Card

Name
Title
Phone no
Mobile no
Address
PO Box
email address
website

Colors
e34197

Requirements
Must have
• Tempate for changing business card personal details including Name, position title, mobile number, email address.
• Keep current logo and colours as per attached
• Logo must be presented in 2 colours or black only not white
Nice to have
• One side logo and graphic only other side logo and personal details
Should not have
• Should not be the same as the current version (attached) but a modern interpretation.
• Does not need a busy reverse side with our list of services as per current version. I feel this is too busy.
• No photos

```html
<!DOCTYPE html>
<html lang="en">
<head>
<meta charset="utf-8">
<title>Staff Compass – Business Card</title>
<link rel="stylesheet" href="https://fonts.googleapis.com/css2?family=Exo+2:wght@400;500;700&display=swap">
<style>
  :root {
    --pink: #e0139f;
    --pink-deep: #c40a8b;
    --pink-light: #ec4dbd;
    --ink: #2b2b2b;
    --grey: #5a5a5a;
    --paper: #ffffff;
    --backdrop: #5b4a3b;
  }
  * { box-sizing: border-box; margin: 0; padding: 0; }
  html, body { width: 1200px; height: 885px; overflow: hidden; }
  body {
    background: var(--backdrop);
    font-family: "Exo 2", sans-serif;
    position: relative;
  }
  .card {
    position: absolute;
    top: 283px;
    width: 520px;
    height: 318px;
    border-radius: 4px;
    overflow: hidden;
    box-shadow: 0 10px 28px rgba(0,0,0,.35);
  }
  /* Front side */
  .card-front { left: 70px; background: var(--paper); }
  .front-brand {
    position: absolute;
    left: 34px; top: 108px;
    display: flex; align-items: center; gap: 10px;
  }
  .brand-dot {
    width: 14px; height: 14px; border-radius: 50%;
    background: var(--pink);
  }
  .brand-name {
    font-weight: 700;
    font-size: 30px;
    color: var(--ink);
    letter-spacing: -.5px;
  }
  .divider {
    position: absolute;
    left: 262px; top: 30px;
    width: 2px; height: 196px;
    background: var(--pink);
  }
  .details {
    position: absolute;
    left: 284px; top: 34px;
  }
  .person-name {
    font-weight: 700;
    font-size: 24px;
    color: var(--pink);
    line-height: 1;
  }
  .person-title {
    font-size: 11px;
    letter-spacing: .6px;
    color: var(--grey);
    margin-top: 5px;
  }
  .contact-list { list-style: none; margin-top: 28px; }
  .contact-list li {
    display: flex; align-items: center; gap: 9px;
    font-size: 14px; color: var(--ink);
    height: 25px;
  }
  .contact-icon { width: 16px; height: 16px; flex: none; }
  .address-band {
    position: absolute;
    left: 0; bottom: 0;
    width: 100%; height: 62px;
    background: linear-gradient(90deg, var(--pink-deep), var(--pink-light));
    display: flex; align-items: center;
    padding-left: 34px;
    color: var(--paper);
    font-size: 19px;
    letter-spacing: .3px;
  }
  /* Back side */
  .card-back {
    left: 610px;
    background: linear-gradient(135deg, var(--pink-deep), var(--pink) 55%, var(--pink-light));
    display: flex; align-items: center; justify-content: center;
  }
  .back-brand { display: flex; align-items: center; gap: 14px; }
  .back-brand .brand-dot { width: 18px; height: 18px; background: var(--paper); }
  .back-brand .brand-name { font-size: 44px; color: var(--paper); }
</style>
</head>
<body>
  <section class="card card-front" aria-label="Business card front">
    <div class="front-brand">
      <span class="brand-dot"></span>
      <span class="brand-name">Staff Compass</span>
    </div>
    <div class="divider"></div>
    <div class="details">
      <p class="person-name">Megan Hale</p>
      <p class="person-title">PRINCIPAL CONSULTANT</p>
      <ul class="contact-list">
        <li>
          <svg class="contact-icon" viewBox="0 0 16 16"><rect width="16" height="16" rx="2" fill="#e0139f"/><path d="M5 4h2l1 2.5-1.2.8a6 6 0 0 0 2 2l.8-1.2L12 9v2a1 1 0 0 1-1 1A7 7 0 0 1 4 5a1 1 0 0 1 1-1z" fill="#fff"/></svg>
          02 5550 1284
        </li>
        <li>
          <svg class="contact-icon" viewBox="0 0 16 16"><rect width="16" height="16" rx="2" fill="#e0139f"/><rect x="5" y="3" width="6" height="10" rx="1" fill="#fff"/><rect x="6" y="4.5" width="4" height="6" fill="#e0139f"/></svg>
          0400 555 210
        </li>
        <li>
          <svg class="contact-icon" viewBox="0 0 16 16"><rect width="16" height="16" rx="2" fill="#e0139f"/><rect x="3" y="4.5" width="10" height="7" fill="#fff"/><path d="M3 4.5l5 4 5-4" fill="none" stroke="#e0139f" stroke-width="1"/></svg>
          megan@staffcompass.com.au
        </li>
        <li>
          <svg class="contact-icon" viewBox="0 0 16 16"><rect width="16" height="16" rx="2" fill="#e0139f"/><circle cx="8" cy="8" r="4.5" fill="none" stroke="#fff" stroke-width="1.2"/><path d="M3.5 8h9M8 3.5c-2 2.5-2 6.5 0 9M8 3.5c2 2.5 2 6.5 0 9" fill="none" stroke="#fff" stroke-width="1"/></svg>
          www.staffcompass.com.au
        </li>
      </ul>
    </div>
    <div class="address-band">P.O. Box 218 Harbour Point, NSW 2400</div>
  </section>

  <section class="card card-back" aria-label="Business card back">
    <div class="back-brand">
      <span class="brand-dot"></span>
      <span class="brand-name">Staff Compass</span>
    </div>
  </section>
</body>
</html>
```